The Q Collective Business Cards

We need a sleek looking business card for our real estate company. Looking for a clean, modern, eye catching design on a standard size business card.
Updates

No more submissions please! Thank you!

Target Market(s)

General Public/Real Estate Clients

Industry/Entity Type

Real Estate

Contact Information for Business Card

Cards will be customized for each agent.

Colors

Designer to choose only greyscale colors for use in the design.

Requirements
Must have
• Black, white, gray color pallet, Photo area for headshot on the front of the card

```html
<!DOCTYPE html>
<html lang="en">
<head>
<meta charset="utf-8">
<title>The Q Collective – Business Card</title>
<link rel="stylesheet" href="https://fonts.googleapis.com/css2?family=Rubik:wght@400;500&family=Roboto:wght@400&display=swap">
<style>
  :root {
    --page: #d9d6d2;
    --card-light: #f1efec;
    --card-mid: #e2dfdb;
    --ink: #1b1b1b;
    --ink-soft: #2c2c2c;
    --rule: #3a3a3a;
    --edge: #121212;
    --photo-warm: #b59a86;
    --photo-light: #e4ddd6;
    --photo-dark: #5a4336;
  }
  * { box-sizing: border-box; margin: 0; padding: 0; }
  html, body { width: 1200px; height: 1054px; overflow: hidden; }
  body {
    background: var(--page);
    position: relative;
    font-family: "Roboto", Arial, sans-serif;
    color: var(--ink);
  }
  .card {
    position: absolute;
    left: 100px; top: 241px;
    width: 1000px; height: 572px;
    border-radius: 26px;
    background: linear-gradient(135deg, var(--card-light) 0%, var(--card-mid) 100%);
    overflow: hidden;
    box-shadow: 0 14px 40px rgba(0,0,0,0.12);
  }
  .card-edge {
    position: absolute;
    left: 0; right: 0; bottom: 0;
    height: 12px;
    background: var(--edge);
  }
  .brand {
    position: absolute;
    left: 48px; top: 52px;
    width: 420px;
  }
  .brand-name {
    display: flex; align-items: center; gap: 16px;
    font-family: "Rubik", Arial, sans-serif;
    font-weight: 400;
    font-size: 50px;
    letter-spacing: 1px;
    color: var(--ink);
    line-height: 1;
  }
  .brand-mark {
    width: 18px; height: 18px;
    background: var(--ink);
    flex: none;
  }
  .brand-tagline {
    margin-top: 26px;
    font-family: "Rubik", Arial, sans-serif;
    font-size: 19px;
    letter-spacing: 6px;
    color: var(--ink-soft);
    text-align: center;
    width: 510px;
  }
  .headshot {
    position: absolute;
    left: 694px; top: 19px;
    width: 296px; height: 374px;
    background:
      radial-gradient(ellipse 38% 34% at 50% 40%, var(--photo-light) 0%, var(--photo-warm) 55%, transparent 80%),
      linear-gradient(180deg, var(--photo-dark) 0%, var(--photo-warm) 60%, var(--photo-light) 100%);
  }
  .agent {
    position: absolute;
    left: 48px; top: 288px;
  }
  .agent-name {
    font-family: "Rubik", Arial, sans-serif;
    font-weight: 500;
    font-size: 40px;
    line-height: 1.1;
  }
  .agent-title {
    margin-top: 4px;
    font-family: "Rubik", Arial, sans-serif;
    font-size: 24px;
    color: var(--ink-soft);
  }
  .divider {
    position: absolute;
    left: 46px; top: 392px;
    width: 910px; height: 2px;
    background: var(--rule);
  }
  .contact-list {
    position: absolute;
    left: 48px; top: 428px;
    list-style: none;
  }
  .contact-item {
    display: flex; align-items: center;
    height: 37.5px;
    font-size: 25px;
  }
  .contact-icon {
    width: 22px; height: 22px;
    margin-right: 27px;
    flex: none;
  }
  .address {
    position: absolute;
    right: 45px; top: 466px;
    text-align: right;
    font-size: 25px;
    line-height: 37.5px;
    font-style: normal;
  }
</style>
</head>
<body>
  <div class="card">
    <div class="brand">
      <div class="brand-name"><span class="brand-mark"></span>The Q Collective</div>
      <div class="brand-tagline">· REAL ESTATE TEAM ·</div>
    </div>

    <div class="headshot" role="img" aria-label="Agent headshot photo"></div>

    <div class="agent">
      <div class="agent-name">Dana Whitfield Moreau</div>
      <div class="agent-title">Real Estate Broker</div>
    </div>

    <div class="divider"></div>

    <ul class="contact-list">
      <li class="contact-item">
        <svg class="contact-icon" viewBox="0 0 24 24" aria-hidden="true">
          <path fill="#1b1b1b" d="M3 8c0-2 4-4 9-4s9 2 9 4v2h-5V8H8v2H3z"/>
          <path fill="#1b1b1b" d="M7 11h10l3 8H4z"/>
          <circle cx="12" cy="15" r="2" fill="#f1efec"/>
        </svg>
        +1 555-201-7764
      </li>
      <li class="contact-item">
        <svg class="contact-icon" viewBox="0 0 24 24" aria-hidden="true">
          <rect x="2" y="5" width="20" height="14" fill="#1b1b1b"/>
          <path d="M2 5l10 8 10-8" fill="none" stroke="#f1efec" stroke-width="1.6"/>
        </svg>
        dana@homefinderbureau.com
      </li>
      <li class="contact-item">
        <svg class="contact-icon" viewBox="0 0 24 24" aria-hidden="true">
          <circle cx="12" cy="12" r="9" fill="#1b1b1b"/>
          <g fill="none" stroke="#f1efec" stroke-width="1.2">
            <ellipse cx="12" cy="12" rx="4" ry="9"/>
            <path d="M3 12h18M5 7.5h14M5 16.5h14"/>
          </g>
        </svg>
        www.homefinderbureau.com
      </li>
    </ul>

    <address class="address">
      4120 Alder Park Rd<br>
      Linwood Bay, LA, US 70900
    </address>

    <div class="card-edge"></div>
  </div>
</body>
</html>
```